IT Consulting Business needs a web design

We need a web design for an IT Consulting company called "Vorensk". We want to replace the existing web site (www.vorensk-example.com) with a new design. Our services are IT Consulting, IT Training, IT Outsourcing.
We would like to see designs that communicate "Trusted IT Advisor" with modern & bold design.

We would like to see the design of 2 pages:
1. Home page (www.vorensk-example.com)
2. The detail page (http://www.vorensk-example.com/index_files/consulting.htm)

Industry/Entity Type

Business

```html
<!DOCTYPE html>
<html lang="en">
<head>
<meta charset="utf-8">
<title>Vorensk – Consulting Services</title>
<link href="https://fonts.googleapis.com/css2?family=PT+Sans:wght@400;700&family=Arimo:wght@400;700&display=swap" rel="stylesheet">
<style>
:root{
  --page:#f4f4f4;
  --blue:#1f63be;
  --blue-deep:#1654a8;
  --red:#d0191f;
  --text:#2f2f2f;
  --nav-text:#555;
  --panel:#e4e4e4;
  --rule:#cfcfcf;
  --footer:#282828;
}
*{margin:0;padding:0;box-sizing:border-box}
html,body{width:1200px;height:925px;overflow:hidden;background:var(--page)}
body{position:relative;font-family:"PT Sans",sans-serif;color:var(--text)}
ul{list-style:none}

.site-header{position:absolute;left:0;top:0;width:1200px;height:70px;background:var(--page);border-bottom:3px solid var(--rule)}
.brand{position:absolute;left:189px;top:14px;font-family:"Arimo",sans-serif;font-weight:700;font-size:30px;color:var(--blue);letter-spacing:-0.5px}
.main-nav{position:absolute;left:550px;top:0;display:flex;height:66px}
.main-nav a{display:flex;align-items:center;height:66px;padding:0 11px;font-size:12.5px;color:var(--nav-text);text-decoration:none;border-left:1px solid #e2e2e2}
.main-nav a:nth-child(2){border-left:none}
.main-nav a.active{background:var(--blue);color:#fff;border-top:5px solid var(--red);padding:0 11px 0 14px;border-left:none}

.hero-band{position:absolute;left:0;top:70px;width:1200px;height:249px;background:linear-gradient(180deg,var(--blue) 0%,#2268c4 60%,var(--blue-deep) 100%)}
.hero-photo{position:absolute;left:189px;top:23px;width:822px;height:203px;background:linear-gradient(90deg,#2a2e36 0%,#3a4250 45%,#3f6fb0 75%,#1f7fe0 100%)}

.content{position:absolute;left:188px;top:346px;width:550px}
.section-title{font-family:"Arimo",sans-serif;font-weight:700;font-size:17.5px;color:var(--blue);line-height:26px}
.section-title span{color:var(--red)}
.lead{font-size:11px;line-height:15.5px;margin-top:5px}
.sub-title{font-size:11px;color:var(--red);margin-top:4px;line-height:16px}
.check-list{margin:4px 0 0 18px}
.check-list li{position:relative;padding-left:13px;font-size:11px;line-height:23.8px}
.check-list li::before{content:"";position:absolute;left:2px;top:9px;width:4px;height:4px;border-right:2px solid var(--red);border-top:2px solid var(--red);transform:rotate(45deg)}

.side-box{position:absolute;left:766px;width:245px;background:var(--panel);border-radius:3px;box-shadow:-4px 0 5px -3px rgba(0,0,0,.18);padding:0 18px 0 19px}
.side-box .section-title{margin-top:4px}
.side-list{margin-top:6px}
.side-list li{position:relative;padding-left:22px;font-size:11px;line-height:18px;margin-bottom:5.5px}
.side-list li::before{content:"";position:absolute;left:3px;top:6px;width:2px;height:2px;background:var(--red);box-shadow:4px 0 var(--red),0 4px var(--red),4px 4px var(--red)}
.side-list li.current{color:var(--red)}
.services-box{top:341px;height:122px;padding-top:9px}
.expertise-box{top:473px;height:211px;padding-top:9px}
.values-box{top:695px;height:122px;padding-top:9px}

.site-footer{position:absolute;left:0;top:842px;width:1200px;height:83px;background:var(--footer)}
.footer-nav{position:absolute;left:187px;top:17px;font-family:"Arimo",sans-serif;font-size:11px;color:#fff;display:flex}
.footer-nav a{color:#fff;text-decoration:none}
.footer-nav a.active{color:#e63a3a}
.footer-nav .sep{margin:0 9px;color:#fff}
.copyright{position:absolute;left:187px;top:36px;font-family:"Arimo",sans-serif;font-size:11px;color:#fff}
.social{position:absolute;left:929px;top:18px;display:flex;gap:3px}
.social span{display:block;width:25px;height:25px;background:var(--red);border-radius:3px}
</style>
</head>
<body>
<header class="site-header">
  <div class="brand">Vorensk</div>
  <nav class="main-nav">
    <a class="active" href="#">HOME</a>
    <a href="#">ABOUT US</a>
    <a href="#">SERVICES</a>
    <a href="#">EXPERTISES</a>
    <a href="#">CAREERS</a>
    <a href="#">CONTACT US</a>
  </nav>
</header>

<section class="hero-band">
  <div class="hero-photo" role="img" aria-label="Banner photo: businessman in suit writing the word technology by hand on a blue digital screen"></div>
</section>

<main class="content">
  <h1 class="section-title"><span>Consulting</span> Services</h1>
  <p class="lead">Our experienced, certified professionals provides IT consulting using industry recommended practices. We are specialized in Corvella Business Productivity Platform using Corvella Portivane Technologies and Business Intelligence Platform.</p>
  <p class="sub-title">Some of our services are</p>
  <ul class="check-list">
    <li>Strategic technology consulting and advice</li>
    <li>Business technology reviews, audits, and studies</li>
    <li>Business technology improvements</li>
    <li>Solution architecture design and implementation for applications of all sizes</li>
  </ul>
  <p class="sub-title">Some of our solutions are</p>
  <ul class="check-list">
    <li>Corporate intranet portal and public web site</li>
    <li>Business intelligence solution</li>
    <li>Enterprise search solution</li>
    <li>Document and record management solution</li>
    <li>Business form and enterprise collaboration solution</li>
    <li>Knowledge management solution</li>
  </ul>
</main>

<aside class="side-box services-box">
  <h2 class="section-title"><span>Our</span> Services</h2>
  <ul class="side-list">
    <li class="current">Consulting Service</li>
    <li>Training Service</li>
    <li>Solution Service</li>
  </ul>
</aside>

<aside class="side-box expertise-box">
  <h2 class="section-title"><span>Our</span> Expertises</h2>
  <ul class="side-list">
    <li>Corvella Portivane Technologies</li>
    <li>Business Intelligence with Corvella Quellbase Server</li>
    <li>Enterprise Integration with Junctara Server</li>
    <li>Ostrel Development</li>
    <li>Tervan Onyx</li>
  </ul>
</aside>

<aside class="side-box values-box">
  <h2 class="section-title"><span>Core</span> Value</h2>
  <ul class="side-list">
    <li>Quality Conscious</li>
    <li>Customer Fouce</li>
    <li>Committed</li>
  </ul>
</aside>

<footer class="site-footer">
  <nav class="footer-nav">
    <a class="active" href="#">Home</a><span class="sep">|</span>
    <a href="#">About Us</a><span class="sep">|</span>
    <a href="#">Services</a><span class="sep">|</span>
    <a href="#">Careers</a><span class="sep">|</span>
    <a href="#">Expertises</a><span class="sep">|</span>
    <a href="#">Contact Us</a>
  </nav>
  <p class="copyright">Vorensk © 2013. All Rights Reserved.</p>
  <div class="social" aria-label="Social links">
    <span></span><span></span><span></span>
  </div>
</footer>
</body>
</html>
```